New, modern business card for growing audiology practice

We need a new business card for our audiology practice. Our logo and website have recently changed (more modern) and we want our business cards to reflect this change.
We conduct hearing tests, perform earwax removals, and fit & dispense hearing aids to our patients. We are a family owned practice in which the owner is the one who works directly with the patient. I have attached logos in various formats to use, as well as two ideas I found on this website; as well as a scanned copy of our current logo. Good luck!

Industry/Entity Type

Business

Contact Information for Business Card

Company name: Tolvera Hearing Center
Provider name: Peter Wolstenby, Au.D. F/NSB
Phone number: (440) 683-5127
Address: 837 W. Lindell Ave. Brenmoor Falls, WI 53917
email: tolverahearing@postvane.com
website: tolverahearing.com

Colors
000000
aaaaaa
dbdbdb
cacaca
9bcb3c
afd23c
cadf82
b1b1b1

Requirements
Must have
• My card must include information in the "details" section. In the attached images, I found a few that I liked and I would like to model after - "brisky bouncin'" and "Sound Method Center".
• Must be horizontal.
• Must include logos provided. I uploaded them in various file formats and various ways.
• Must match logo font, if possible, if not, please get as close as you can.
Nice to have
• I really like the idea of having a color on one side with just the logo and company name and the contact information and provider name on the other side. I also really like the idea of having the main color dominating on the logo/company side with accent of that same color on the contact side of the card.
Should not have
• Must not be vertical.

```html
<!DOCTYPE html>
<html lang="en">
<head>
<meta charset="utf-8">
<title>Tolvera Hearing Center – Business Card</title>
<link rel="stylesheet" href="https://fonts.googleapis.com/css2?family=Open+Sans:wght@400;700&display=swap">
<style>
  :root {
    --page-bg: #e4e4e2;
    --card-bg: #f3f3f1;
    --brand-green: #78a640;
    --ink: #1e1e1e;
    --on-green: #ffffff;
  }
  * { box-sizing: border-box; margin: 0; padding: 0; }
  html, body {
    width: 1200px;
    height: 900px;
    overflow: hidden;
    background: var(--page-bg);
    font-family: "Open Sans", Arial, sans-serif;
  }
  .canvas {
    position: relative;
    width: 1200px;
    height: 900px;
  }
  .business-card {
    position: absolute;
    left: 100px;
    top: 165px;
    width: 1000px;
    height: 570px;
    background: var(--card-bg);
    box-shadow: 0 14px 40px rgba(0,0,0,0.18);
    overflow: hidden;
  }
  .brand-side {
    position: absolute;
    left: 0; top: 0;
    width: 560px;
    height: 100%;
  }
  .brand-lockup {
    position: absolute;
    left: 44px;
    top: 394px;
    display: flex;
    align-items: center;
    gap: 16px;
  }
  .brand-dot {
    width: 26px;
    height: 26px;
    border-radius: 50%;
    background: var(--brand-green);
    flex: none;
  }
  .brand-name {
    font-size: 30px;
    font-weight: 400;
    letter-spacing: 0.3px;
    text-transform: uppercase;
    color: var(--ink);
    white-space: nowrap;
  }
  .contact-side {
    position: absolute;
    left: 560px; top: 0;
    width: 440px;
    height: 100%;
    background: var(--brand-green);
    color: var(--on-green);
    text-align: right;
  }
  .provider-name {
    position: absolute;
    right: 28px;
    top: 62px;
    font-size: 29px;
    font-weight: 700;
    letter-spacing: 0.5px;
    text-transform: uppercase;
    white-space: nowrap;
  }
  .provider-credentials {
    position: absolute;
    right: 28px;
    top: 104px;
    font-size: 22px;
    text-transform: uppercase;
    white-space: nowrap;
  }
  .address {
    position: absolute;
    right: 28px;
    top: 302px;
    font-size: 25px;
    line-height: 37px;
    font-style: normal;
    white-space: nowrap;
  }
  .contact-list {
    position: absolute;
    right: 28px;
    top: 448px;
    list-style: none;
    font-size: 24px;
    line-height: 37px;
    white-space: nowrap;
  }
  .contact-list li {
    display: flex;
    justify-content: flex-end;
    align-items: center;
    gap: 8px;
  }
  .contact-icon {
    width: 20px;
    height: 20px;
    flex: none;
  }
</style>
</head>
<body>
<div class="canvas">
  <section class="business-card" aria-label="Tolvera Hearing Center business card">
    <div class="brand-side">
      <div class="brand-lockup">
        <span class="brand-dot"></span>
        <span class="brand-name">Tolvera Hearing Center</span>
      </div>
    </div>
    <div class="contact-side">
      <h1 class="provider-name">Peter Wolstenby,</h1>
      <p class="provider-credentials">Au.D. F/NSB</p>
      <address class="address">
        837 W. Lindell<br>
        Ave. Brenmoor Falls,<br>
        WI 53917
      </address>
      <ul class="contact-list">
        <li>(440) 683-5127
          <svg class="contact-icon" viewBox="0 0 24 24" aria-hidden="true"><path fill="#fff" d="M6.6 10.8c1.4 2.8 3.8 5.1 6.6 6.6l2.2-2.2c.3-.3.7-.4 1-.2 1.1.4 2.3.6 3.6.6.6 0 1 .4 1 1V20c0 .6-.4 1-1 1C10.6 21 3 13.4 3 4c0-.6.4-1 1-1h3.5c.6 0 1 .4 1 1 0 1.3.2 2.5.6 3.6.1.3 0 .7-.2 1z"/></svg>
        </li>
        <li>tolverahearing@postvane.com
          <svg class="contact-icon" viewBox="0 0 24 24" aria-hidden="true"><rect x="2" y="5" width="20" height="14" fill="#fff"/><path d="M2 5l10 8 10-8" fill="none" stroke="#78a640" stroke-width="1.6"/></svg>
        </li>
        <li>www.tolverahearing.com
          <svg class="contact-icon" viewBox="0 0 24 24" aria-hidden="true"><circle cx="12" cy="12" r="10" fill="#fff"/><path d="M2 12h20M12 2c3 3 3 17 0 20M12 2c-3 3-3 17 0 20" fill="none" stroke="#78a640" stroke-width="1.4"/></svg>
        </li>
      </ul>
    </div>
  </section>
</div>
</body>
</html>
```